Design a Website in Wordpress for an Australian Health Training Company in Health related courses

We require a WORDPRESS based Website (due to add on's we need to use for third party software) to replace our old site.
We offer national face to face delivery in medical reception, terminology and also administration.
The website will have around 6 pages and the ability to describe our main 6 courses (perhaps on the Courses page this may be tabs opening up to details for example?)
I have attached a previous sample of a Joomla site which was being developed (please do not feel you have to copy this - but I am just giving it as a sample - copying would be boring). But it gives an idea of look/feel and colours which may be suitable. Open to other ideas though.
I will provide some of the content, but would like the ability to finish the content myself.
Images and graphics are important. While a few medical photos re great - don't be tempted to us all pictures of doctors and nurses (although a couple would be good) - these are administrative courses so general corporate, eye catching visionary pictures of people in general are great. A medical type picture is also fine.
THE BOOKING system - will be via an ADD ON which will occur at the end of the project and is supplied by a third party software company (our student management system). This project will include up to 2 hours working with the Tech guys from the third party software to enable the ADD ON. If this ADD ON requires more time, we will pay hourly (although I do not expect it will).
Target Market(s)
Mostly a female market, many mature aged women target 25-45 yrs. Mixture of medical/health and corporate. Maybe a bit of mums returning to work and corporate inspiration.
Industry/Entity Type
It Company
Coding
Coded - Design and coding required
Number of Pages Required
5+ page
Requirements
Must have
- Wordpress
- Great graphics
- Interesting
- professional and clean
- Enquiry section (info Pak)
- Should have a University feel to it - Education
- Pages
- Home Page - About Us - Recruitment -Courses - Class Schedule - Traineeships Queensland Funding - Latest News Blog - Corporate Training- Contact us

```html
<!DOCTYPE html>
<html lang="en">
<head>
<meta charset="utf-8">
<title>Harbourline Institute of Training</title>
<link href="https://fonts.googleapis.com/css2?family=Raleway:wght@400;500;600;700&display=swap" rel="stylesheet">
<style>
:root{
  --blue:#0b4ea2;
  --blue-mid:#2f6fc0;
  --navy:#133a6b;
  --orange:#f79a3b;
  --orange-light:#fbb46b;
  --ink:#333;
  --muted:#666;
  --link:#2f6fc0;
  --footer:#3b3b3b;
  --footer-deep:#2e2e2e;
  --white:#fff;
}
*{box-sizing:border-box;margin:0;padding:0}
html,body{width:1200px;height:2483px;overflow:hidden;background:#fff}
body{font-family:"Raleway",Arial,sans-serif;color:var(--ink);position:relative}
section,header,footer{position:absolute;left:0;width:1200px}
.abs{position:absolute}

/* header */
.site-header{top:0;height:112px;background:#fff;border-top:3px solid var(--blue);z-index:3}
.brand{position:absolute;left:84px;top:0;width:198px;height:193px;background:#fff;border-radius:0 0 99px 99px;box-shadow:0 2px 6px rgba(0,0,0,.12);display:flex;align-items:center;justify-content:center;text-align:center}
.brand-name{font-weight:700;color:var(--navy);font-size:17px;line-height:1.25;letter-spacing:1px;text-transform:uppercase}
.main-nav{position:absolute;left:306px;top:52px;display:flex}
.main-nav a{font-size:11px;color:#333;text-decoration:none;margin-right:24px;font-weight:500}
.main-nav a.active{color:var(--blue);font-weight:700}
.btn-enroll,.btn-info{position:absolute;left:1014px;width:96px;height:32px;color:#fff;font-size:13px;font-weight:600;display:flex;align-items:center;justify-content:center}
.btn-enroll{top:20px;background:var(--blue)}
.btn-info{top:62px;background:var(--orange)}

/* hero */
.hero{top:112px;height:448px;background:linear-gradient(180deg,#3d4f63 0%,#6d6f74 35%,#b98650 68%,#d98a2c 82%,#111 100%)}
.hero-mark{position:absolute;left:735px;top:40px;width:280px;text-align:center;color:rgba(255,255,255,.35);font-weight:700;font-size:22px;line-height:1.2;letter-spacing:1px;text-transform:uppercase}
.hero-cta{position:absolute;left:766px;top:324px;width:222px;height:42px;border:2px solid #fff;color:#fff;font-size:19px;font-weight:600;display:flex;align-items:center;justify-content:center}
.hero-arrow{position:absolute;top:205px}

/* courses */
.courses{top:560px;height:322px;background:var(--blue);color:#fff}
.section-title{position:absolute;left:0;width:1200px;text-align:center;font-size:24px;font-weight:600}
.course{position:absolute;top:117px;width:170px;text-align:center}
.course-ring{width:96px;height:96px;border:2px solid #fff;border-radius:50%;margin:0 auto;display:flex;align-items:center;justify-content:center}
.course-label{margin-top:22px;font-size:16px;line-height:1.6}

/* blog */
.blog{top:882px;height:581px;background:#fff}
.blog .section-title{color:var(--navy)}
.post{position:absolute;top:136px;width:314px}
.post-image{width:314px;height:182px;border:2px solid #ddd;position:relative}
.post-date{position:absolute;left:0;top:0;width:70px;height:56px;background:rgba(11,78,162,.85);color:#fff;font-size:15px;line-height:22px;padding:6px 9px;white-space:nowrap}
.post-title{margin-top:16px;width:270px;font-size:17px;line-height:1.65;color:#333;font-weight:500}
.post-meta{margin-top:12px;font-size:11.5px;color:#333}
.post-meta span{color:var(--link)}
.post-text{margin-top:14px;font-size:11.5px;line-height:2;color:#555;width:300px}
.read-more{position:absolute;right:10px;top:392px;font-size:11.5px;color:var(--link)}

/* info pack and why */
.enquiry{top:1463px;height:424px;width:600px;background:linear-gradient(135deg,#2f6fc0,#2662b4)}
.enquiry h2{position:absolute;left:100px;top:34px;color:#fff;font-size:20px;font-weight:600}
.field{position:absolute;left:100px;width:461px;height:42px;border:1px solid rgba(255,255,255,.6);color:#e4ecf7;font-size:13px;padding:12px}
.send{position:absolute;left:100px;top:352px;width:122px;height:34px;background:#fff;color:var(--blue);font-size:14px;display:flex;align-items:center;justify-content:center}
.why{top:1463px;left:600px;height:424px;width:600px;background:linear-gradient(180deg,var(--orange-light),var(--orange))}
.why h2{position:absolute;left:40px;top:34px;color:#fff;font-size:20px;font-weight:600}
.why-item{position:absolute;left:40px;width:470px;color:#fff}
.why-item h3{font-size:16px;font-weight:500}
.why-item p{margin-top:10px;font-size:11px;line-height:2}
.dots{position:absolute;left:40px;top:390px;display:flex;gap:6px}
.dots i{width:8px;height:8px;border-radius:50%;background:#fff}
.dots i.on{background:var(--blue)}

/* testimonials */
.testimonials{top:1887px;height:275px;background:#fff}
.testimonials h2{position:absolute;left:119px;top:56px;font-size:24px;font-weight:600;color:var(--navy)}
.rule{position:absolute;left:346px;top:72px;width:728px;height:1px;background:#ddd}
.quote-text{position:absolute;left:328px;top:130px;width:772px;font-size:12px;line-height:2.15;color:#555}
.quote-author{position:absolute;left:328px;top:218px;font-size:15px;color:var(--link)}

/* footer */
.site-footer{top:2162px;height:248px;background:var(--footer);color:#fff}
.footer-brand{position:absolute;left:98px;top:48px;width:164px;text-align:center;font-weight:700;font-size:15px;line-height:1.3;letter-spacing:1px;text-transform:uppercase}
.footer-col{position:absolute;top:42px}
.footer-col h4{font-size:14px;font-weight:500;margin-bottom:14px}
.footer-col li{list-style:none;font-size:12px;line-height:27.5px}
.footer-col li::before{content:"»";margin-right:10px}
.contact li::before{content:none}
.contact li{display:flex;gap:14px;line-height:1.8;margin-bottom:14px;white-space:nowrap}
.social{display:flex;gap:12px}
.social i{width:36px;height:36px;border:2px solid #fff;border-radius:50%;display:block}
.bottom-bar{position:absolute;left:0;top:2410px;width:1200px;height:73px;background:var(--footer-deep);color:#fff;font-size:12px;display:flex;align-items:center;justify-content:center}
</style>
</head>
<body>

<header class="site-header">
  <div class="brand"><div class="brand-name">Harbourline<br>Institute<br>of Training</div></div>
  <nav class="main-nav">
    <a class="active">Home</a><a>About Us</a><a>Recruitment</a><a>Courses</a><a>Class Schedule</a><a>Funding</a><a>Blog</a><a>Corporate Training</a><a>Contact us</a>
  </nav>
  <div class="btn-enroll">Enroll Now</div>
  <div class="btn-info">Info Pack</div>
</header>

<section class="hero" role="img" aria-label="Silhouette of a runner against a sunset sky over a grassy field">
  <div class="hero-mark">Harbourline<br>Institute of Training</div>
  <div class="hero-cta">Make Your Enquiry</div>
  <svg class="hero-arrow" style="left:44px" width="24" height="44" viewBox="0 0 24 44"><path d="M22 2 2 22l20 20" fill="none" stroke="#fff" stroke-width="2"/></svg>
  <svg class="hero-arrow" style="left:1134px" width="24" height="44" viewBox="0 0 24 44"><path d="M2 2l20 20L2 42" fill="none" stroke="#fff" stroke-width="2"/></svg>
</section>

<section class="courses">
  <h2 class="section-title" style="top:40px">Our List Of Courses</h2>
  <div class="course" style="left:80px"><div class="course-ring"><svg width="44" height="40" viewBox="0 0 44 40"><rect x="2" y="9" width="40" height="29" rx="3" fill="#fff"/><rect x="14" y="3" width="16" height="7" rx="2" fill="none" stroke="#fff" stroke-width="3"/><path d="M22 16v15M14.5 23.5h15" stroke="#0b4ea2" stroke-width="5"/></svg></div><div class="course-label">Medical Reception<br>&amp; Terminology</div></div>
  <div class="course" style="left:254px"><div class="course-ring"><svg width="46" height="46" viewBox="0 0 46 46"><circle cx="23" cy="23" r="20" fill="none" stroke="#fff" stroke-width="3"/><path d="M23 3v20h20" fill="none" stroke="#fff" stroke-width="3"/></svg></div><div class="course-label">Cert III Business<br>Administration</div></div>
  <div class="course" style="left:428px"><div class="course-ring"><svg width="50" height="42" viewBox="0 0 50 42"><rect x="4" y="6" width="34" height="16" rx="8" transform="rotate(30 21 14)" fill="none" stroke="#fff" stroke-width="3"/><rect x="22" y="24" width="26" height="14" rx="7" fill="#fff"/></svg></div><div class="course-label">Medical<br>Terminology</div></div>
  <div class="course" style="left:600px"><div class="course-ring"><svg width="50" height="32" viewBox="0 0 50 32"><rect x="2" y="2" width="46" height="28" rx="3" fill="none" stroke="#fff" stroke-width="3"/><path d="M9 10h4M17 10h4M25 10h4M33 10h4M9 16h4M17 16h4M25 16h4M33 16h4M12 23h26" stroke="#fff" stroke-width="3"/></svg></div><div class="course-label">Keyboard and<br>Typing</div></div>
  <div class="course" style="left:772px"><div class="course-ring"><svg width="46" height="44" viewBox="0 0 46 44"><rect x="4" y="4" width="36" height="24" rx="3" fill="none" stroke="#fff" stroke-width="3"/><path d="M4 12h36" stroke="#fff" stroke-width="4"/><circle cx="30" cy="30" r="11" fill="#fff"/><path d="M30 24v12" stroke="#0b4ea2" stroke-width="2.5"/></svg></div><div class="course-label" style="margin-top:30px">Harbourline Online</div></div>
  <div class="course" style="left:949px"><div class="course-ring"><svg width="42" height="50" viewBox="0 0 42 50"><rect x="6" y="8" width="30" height="38" rx="4" fill="none" stroke="#fff" stroke-width="3"/><rect x="14" y="3" width="14" height="8" rx="2" fill="#fff"/><path d="M13 28l6 6 10-12" fill="none" stroke="#fff" stroke-width="3"/></svg></div><div class="course-label" style="margin-top:30px">Confidentiality</div></div>
</section>

<section class="blog">
  <h2 class="section-title" style="top:56px">Our Blog Post</h2>
  <article class="post" style="left:100px">
    <div class="post-image" role="img" aria-label="Group fitness class exercising in a bright gym" style="background:linear-gradient(135deg,#b9c6cf,#7e9aa8 55%,#c45a55)"><div class="post-date">May 17<br>2016</div></div>
    <h3 class="post-title">An wisi appareat gloriaturme ea mel hendrerit</h3>
    <p class="post-meta"><span>Added on  May 17 , 2016</span>  at 12:41</p>
    <p class="post-text">There’s a thin red line between social media use and networking. Sometimes the two merge into a perfect harmony of conversation and resolution.</p>
    <div class="read-more">[ Read more ]</div>
  </article>
  <article class="post" style="left:443px">
    <div class="post-image" role="img" aria-label="Team of healthcare workers in uniforms" style="background:linear-gradient(135deg,#eef1f4,#c9d6e2 50%,#5f86b3)"><div class="post-date">May 17<br>2016</div></div>
    <h3 class="post-title">Pro ei dolorem vocibus voluptuave Tantas labores</h3>
    <p class="post-meta"><span>Added on  May 03 , 2016</span>  at 15:41</p>
    <p class="post-text">Odio vivendum mediocrem cum et, lobortis partiendo repudiandae id pro, mel amet semper sanctus in. Alterum ocurreret sea ex.</p>
    <div class="read-more">[Read more ]</div>
  </article>
  <article class="post" style="left:786px">
    <div class="post-image" role="img" aria-label="Woman training with ropes in a gym" style="background:linear-gradient(135deg,#3b3f46,#6b5d5a 55%,#c97c8c)"><div class="post-date">May 17<br>2016</div></div>
    <h3 class="post-title">An wisi appareat gloriaturme ea mel hendrerit</h3>
    <p class="post-meta"><span>Added on  April 08 , 2016</span>  at 15:18</p>
    <p class="post-text">Odio vivendum mediocrem cum et, lobortis partiendo repudiandae id pro, mel amet semper sanctus in. Alterum ocurreret sea ex.</p>
    <div class="read-more">[ Read more ]</div>
  </article>
</section>

<section class="enquiry">
  <h2>EMAIL me an Info Pack</h2>
  <div class="field" style="top:90px">Name</div>
  <div class="field" style="top:139px">Mobile</div>
  <div class="field" style="top:188px">Email</div>
  <div class="field" style="top:237px">Course</div>
  <div class="field" style="top:286px">State</div>
  <div class="send">Send Now</div>
</section>

<section class="why">
  <h2>Why Harbourline Institute ?</h2>
  <div class="why-item" style="top:80px"><h3>›  Quality</h3><p>Harbourline delivery quality, effective training facilitated by industry leaders. Just ask our students who rate us on average of 4.7 out of 5.</p></div>
  <div class="why-item" style="top:180px"><h3>›  Experience</h3><p>Harbourline is Australia’s largest and leading providers of nationally recognised training in health administration – training from over 17 locations Australia wide.</p></div>
  <div class="why-item" style="top:282px"><h3>›  Value</h3><p>Our innovative teaching approach allows us to deliver exceptional training at affordable prices with no hidden extras.</p></div>
  <div class="dots"><i></i><i class="on"></i><i></i></div>
</section>

<section class="testimonials">
  <h2>Our Testimonials</h2>
  <div class="rule"></div>
  <svg class="abs" style="left:1080px;top:64px" width="22" height="14" viewBox="0 0 22 14"><path d="M7 2 2 7l5 5M15 2l5 5-5 5" fill="none" stroke="#999" stroke-width="1.5"/></svg>
  <div class="abs" style="left:100px;top:134px;width:100px;height:100px;border-radius:50%;background:#9a9a9a"></div>
  <svg class="abs" style="left:114px;top:170px" width="34" height="26" viewBox="0 0 34 26"><path d="M2 14a10 10 0 0 1 10-12v5a5 5 0 0 0-5 5h5v12H2zM20 14a10 10 0 0 1 10-12v5a5 5 0 0 0-5 5h5v12H20z" fill="#fff"/></svg>
  <div class="abs" role="img" aria-label="Portrait of a smiling student wearing glasses" style="left:160px;top:128px;width:116px;height:116px;border-radius:50%;border:4px solid #fff;background:radial-gradient(circle at 50% 40%,#e8cdb8,#8a6a55 75%);box-shadow:0 1px 4px rgba(0,0,0,.2)"></div>
  <p class="quote-text">I completed the course on Feb 13th. Loved it. The trainers, Rhea and Joan were excellent in their delivery and knowledge. I want to say a huge thank you for the course and knowledge I came away with. I have secured a fantastic job after my first application! Such good value for money too! I would highly recommend it. I’m a mature age person so it’s never too late to up -skill yourself to get what you deserve!</p>
  <div class="quote-author">– Mara Ellison</div>
</section>

<footer class="site-footer">
  <div class="footer-brand">Harbourline<br>Institute<br>of Training</div>
  <div class="footer-col" style="left:339px"><h4>MENUS</h4><ul><li>Home</li><li>About us</li><li>Our services</li><li>Blog</li><li>Contact us</li></ul></div>
  <div class="footer-col" style="left:493px"><h4>QUICK LINKS</h4><ul><li>Site map</li><li>Terms and Conditions</li><li>Disclaimer</li><li>Privacy Policy</li><li>Contact us</li></ul></div>
  <div class="footer-col contact" style="left:689px;width:210px"><h4>CONTACT US</h4><ul>
    <li><svg width="16" height="14" viewBox="0 0 16 14"><path d="M8 1 1 7h2v6h4V9h2v4h4V7h2z" fill="#fff"/></svg><span>48 Kestrel Row | Larkfield<br>QLD 4102</span></li>
    <li><svg width="16" height="16" viewBox="0 0 16 16"><rect x="4" y="1" width="8" height="14" rx="1.5" fill="#fff"/><rect x="5.5" y="3" width="5" height="8" fill="#3b3b3b"/></svg><span>Call Us : (07) 5550 1942</span></li>
    <li><svg width="16" height="12" viewBox="0 0 16 12"><rect x="1" y="1" width="14" height="10" fill="none" stroke="#fff" stroke-width="1.5"/><path d="M1 1l7 6 7-6" fill="none" stroke="#fff" stroke-width="1.5"/></svg><span>info@harbourline.example</span></li>
  </ul></div>
  <div class="footer-col" style="left:921px"><h4>CONNECT US WITH</h4><div class="social"><i></i><i></i><i></i><i></i></div></div>
</footer>
<div class="bottom-bar">© &nbsp;Harbourline Training 2016 . All Rights Reserved</div>

</body>
</html>
```